EB-5 Regional Center needs a Web design

Harlow Ridge Financial Partners is an expanding EB-r regional center. We have been successful in sponsoring multiple projects of third-party developers and placing EB-5, B-1, and Private Investments into multiple projects.

We are now partnering directly with project developers in the energy and healthcare to raise foreign capital for projects in those industries. The foreign capital is used as project equity and our collective balance sheets are used to guarantee debt to complete the funding of the projects.

We need a web site where we can post our company credentials, the bios of each partner, a document page for each of our projects where we can post specific project related documents which foreign investors can read, and we will need a section where foreign investors can fill out investor forms confirming that they are qualified investors and leaving their contact so that our agents and executives can make contact.

The final design should reflect the exceptional experience of the partners and our financial strength and stability.

We do have a logo we would want to use on the web design.

Target Market(s)

EB-5 Investors, B-1 Investors, Private Equity and other investors seeking quality investment in job creating US projects.

Coding

Number of Pages Required

5+ page

Font styles to use
Sans Serif

Requirements
Must have
• Pages to display company info, partner bios, projects completed, and a projects in-process page where we can post documents and info on projects for which we are seeking foreign investment. We also need a section where investors can enter their qualifying personal information and leave contact information for us.

```html
<!DOCTYPE html>
<html lang="en">
<head>
<meta charset="utf-8">
<title>Harlow Ridge Financial Partners</title>
<link href="https://fonts.googleapis.com/css2?family=Raleway:wght@400;500;600;700&family=Roboto:wght@500;700&family=Tinos&display=swap" rel="stylesheet">
<style>
:root{
  --accent:#f2775d;
  --accent-soft:#f59a84;
  --ink:#333333;
  --heading:#6a6a6a;
  --muted:#8a8a8a;
  --band:#3c3c3c;
  --footer:#2a2a2a;
  --white:#ffffff;
  --line:#e6e6e6;
  --sans:'Raleway',sans-serif;
  --display:'Roboto',sans-serif;
  --serif:'Tinos',serif;
}
*{box-sizing:border-box;margin:0;padding:0}
html,body{width:1200px;height:4666px;overflow:hidden}
body{font-family:var(--sans);color:var(--ink);background:var(--white);position:relative}
.abs{position:absolute}
.photo{position:absolute}
.btn{position:absolute;display:flex;align-items:center;justify-content:center;gap:8px;background:var(--accent);color:var(--white);font-size:15px;font-weight:600;text-transform:uppercase;z-index:2}
.btn-outline{background:transparent;border:2px solid rgba(255,255,255,.8)}

/* hero */
.hero{position:absolute;left:0;top:0;width:1200px;height:606px;background:linear-gradient(100deg,#4a3a2c 0%,#2c3542 45%,#1f2b3a 70%,#3a2f28 100%);overflow:hidden}
.brand{position:absolute;display:flex;align-items:center;gap:12px;color:var(--white);font-weight:700;font-size:22px;letter-spacing:.5px;line-height:22px}
.brand small{display:block;font-size:12px;font-weight:500;letter-spacing:2px;line-height:16px}
.brand-dot{width:34px;height:34px;border-radius:50%;background:var(--white);flex:none}
.nav{position:absolute;left:450px;top:31px;display:flex;gap:20px;font-size:15px;color:var(--white);font-weight:500}
.nav .active{color:var(--accent)}
.quote{position:absolute;left:85px;top:172px;width:496px;height:234px;border:1px solid rgba(255,255,255,.7);padding:26px 26px;color:var(--white);font-size:17px;line-height:33px;text-align:justify}
.quote em{font-style:normal;color:var(--accent);font-family:var(--serif);font-size:20px}
.quote em.plain{font-family:var(--sans);font-size:17px}
.dots{position:absolute;left:111px;top:520px;display:flex;gap:8px;align-items:center}
.dots i{width:11px;height:11px;border-radius:50%;background:#cfcfcf;display:block}
.dots i.on{width:15px;height:15px;background:var(--accent)}

/* forms + welcome */
.forms{position:absolute;left:0;top:606px;width:353px;height:639px;background:linear-gradient(160deg,#f07a60,#f5a08b);padding:80px 47px 0;color:var(--white)}
.forms h2{font-family:var(--display);font-size:21px;font-weight:500}
.forms p{font-size:13px;line-height:25px;margin:8px 0 16px}
.field{height:40px;border:1px solid rgba(255,255,255,.85);margin-bottom:7px;font-size:13px;padding:10px 14px;display:flex;justify-content:space-between}
.field.tall{height:78px}
.submit{height:40px;border:1px solid rgba(255,255,255,.85);display:flex;align-items:center;justify-content:center;font-weight:600;font-size:15px;margin-top:8px}
.welcome{position:absolute;left:382px;top:684px;width:710px}
.welcome .kicker{font-size:21px;font-weight:600;display:inline-block;border-bottom:2px solid var(--accent);padding-bottom:4px}
.welcome h1{font-family:var(--display);font-size:38px;color:var(--heading);margin:10px 0 12px 40px;font-weight:700}
.welcome p{margin-left:40px;font-size:14px;line-height:25.5px;color:var(--muted)}

/* section heads */
.sec-head{position:absolute;left:0;width:1200px;text-align:center}
.sec-head .kicker{font-size:20px;font-weight:600;display:inline-block;border-bottom:2px solid var(--accent);padding-bottom:3px}
.sec-head h2{font-family:var(--display);font-size:37px;color:var(--heading);margin-top:8px;font-weight:700}
.criteria{position:absolute;top:1433px;left:100px;width:1000px;display:flex;justify-content:space-between}
.criterion{width:310px;text-align:center}
.criterion .bar{width:36px;height:3px;background:var(--accent);margin:0 auto 16px}
.criterion h3{font-size:16px;font-weight:600;line-height:26px;height:52px;padding:0 40px}
.criterion p{font-size:14px;line-height:28px;color:var(--muted);margin-top:10px}

/* services grid */
.services{position:absolute;left:0;top:1765px;width:1200px;display:grid;grid-template-columns:repeat(4,298px);gap:3px;}
.tile{position:relative;height:238px;color:var(--white);overflow:hidden}
.tile .txt{position:absolute;left:9px;bottom:14px;right:10px}
.tile h3{font-family:var(--serif);font-size:18px;font-weight:400;margin-bottom:6px;white-space:nowrap;letter-spacing:.3px}
.tile p{font-size:13px;line-height:23px;width:200px}
.tile svg{position:absolute;right:12px;bottom:24px}

/* projects */
.projects-title{position:absolute;left:110px;top:2320px;font-family:var(--display);font-size:38px;color:var(--heading);font-weight:700}
.rule{position:absolute;height:2px;background:var(--accent);z-index:2}
.projects-copy{position:absolute;left:450px;top:2325px;width:636px;font-size:13.5px;line-height:28px;color:var(--muted);text-align:justify}
.projects-copy p+p{margin-top:10px}

/* team */
.team{position:absolute;left:0;top:3063px;width:1200px;height:533px;background:linear-gradient(90deg,#3f3f3f,#4a4a4a 50%,#3a3a3a)}
.team-title{position:absolute;left:110px;top:213px;font-family:var(--display);font-size:34px;color:var(--white);font-weight:500;z-index:2}
.member{position:absolute;left:571px;top:137px;width:516px;color:#dddddd;font-size:13.5px;line-height:28px}
.member h3{font-family:var(--serif);color:var(--white);font-size:21px;font-weight:400;margin-bottom:8px}
.member p+p{margin-top:12px}

/* news */
.card{position:absolute;top:3790px;width:310px;height:373px;background:#f7f7f7;padding:10px}
.card .pic{height:180px}
.card .bar{width:36px;height:3px;background:var(--accent);margin:18px 0 6px}
.card h3{font-size:17px;font-weight:500;line-height:28px;color:#444;text-transform:uppercase}
.card p{font-size:13.5px;line-height:24px;color:var(--muted);text-align:justify;margin-top:4px}
.card .more{font-size:13px;font-weight:600;margin-top:10px;display:flex;align-items:center;gap:6px}

/* footer */
.footer{position:absolute;left:0;top:4250px;width:1200px;height:416px;background:var(--footer);color:var(--white)}
.footer h4{font-size:15px;font-weight:700;margin-bottom:18px}
.footer p,.footer li{font-size:13.5px;line-height:28px}
.footer ul{list-style:none}
.contact li{display:flex;gap:14px;align-items:flex-start;margin-bottom:8px}
.socials{display:flex;gap:7px;margin-top:14px}
.socials i{width:32px;height:32px;border-radius:50%;background:var(--white);display:block}
.subscribe{display:flex;height:44px;border-radius:22px;background:var(--white);overflow:hidden;width:263px;margin-top:20px}
.subscribe span{flex:1;color:#999;font-size:13px;display:flex;align-items:center;padding-left:20px}
.subscribe b{width:48px;background:var(--accent);display:flex;align-items:center;justify-content:center}
.legal{position:absolute;left:110px;right:113px;top:370px;display:flex;justify-content:space-between;font-size:13px}
</style>
</head>
<body>

<header class="hero">
  <div class="photo" role="img" aria-label="Smiling investor working at a laptop in a warmly lit office at night" style="left:330px;top:60px;width:870px;height:546px;background:radial-gradient(ellipse at 55% 40%,rgba(190,150,110,.45),rgba(40,50,65,0) 60%)"></div>
  <div class="brand" style="left:110px;top:16px"><span class="brand-dot"></span><span>Harlow Ridge<small>Financial Partners</small></span></div>
  <nav class="nav">
    <span class="active">ABOUT</span><span>SERVICES</span><span>PARTNER</span><span>CONTACT US</span>
  </nav>
  <div class="btn btn-outline" style="left:815px;top:17px;width:132px;height:47px;border-width:1px;font-weight:500">
    <svg width="12" height="14" viewBox="0 0 12 14"><circle cx="6" cy="4" r="3.2" fill="#fff"/><path d="M0 14c0-4 2.7-6 6-6s6 2 6 6z" fill="#fff"/></svg>Login</div>
  <div class="btn" style="left:956px;top:17px;width:132px;height:47px;font-weight:500">
    <svg width="14" height="14" viewBox="0 0 14 14" fill="none" stroke="#fff" stroke-width="1.6"><rect x="1" y="3" width="10" height="10"/><path d="M6 8l6-6"/></svg>Sign up</div>
  <div class="quote">THE <em>TRICK IS NOT TO LEARN</em> to trust your gut feelings, but <em>RATHER</em> to discipline yourself to ignore them. Stand by your stocks as long as the fundamental story of <em class="plain">the company hasn't changed."</em></div>
  <div class="btn" style="left:185px;top:379px;width:132px;height:44px;font-weight:500">Read more</div>
  <div class="dots"><i></i><i class="on"></i><i></i><i></i></div>
</header>

<section class="forms">
  <h2>INVESTOR FORMS</h2>
  <p>Lorem ipsumconsectetur adipiscing elit, sed do eiusmod tempor</p>
  <div class="field">Name</div>
  <div class="field">phone</div>
  <div class="field">Email</div>
  <div class="field">Company<svg width="10" height="10" viewBox="0 0 10 10"><path d="M1 3l4 4 4-4" stroke="#fff" fill="none"/></svg></div>
  <div class="field">Subject</div>
  <div class="field tall">Commend</div>
  <div class="submit">SUBMIT</div>
</section>

<section class="welcome">
  <span class="kicker">Welcome to</span>
  <h1>HARLOW RIDGE</h1>
  <p>Lorem ipsum dolor sit amet, consectetur adipiscing elit, sed do eiusmod tempor incididuntlabore et dolore magna aliqua. Quis ipsum suspendisse ultrices gravida. Risus maecelacus vel facilisis. Lorem ipsum dolor sit amet, consectetur adipiscing elit, sed do eiusmod tempor incididntlabore et dolore magna aliqua. Quis ipsum suspendisse ultrices gravida.</p>
</section>
<div class="photo" role="img" aria-label="Laptop showing financial charts on a desk" style="left:356px;top:898px;width:277px;height:172px;background:linear-gradient(135deg,#3d4a5c,#c9a27a)"></div>
<div class="photo" role="img" aria-label="Glowing light bulb beside stacked coins" style="left:356px;top:1074px;width:277px;height:171px;background:linear-gradient(135deg,#5c5248,#d8c3a0)"></div>
<div class="photo" role="img" aria-label="Hand using a calculator over printed financial reports" style="left:637px;top:898px;width:563px;height:347px;background:linear-gradient(135deg,#6b4c3a,#c8b8a8 55%,#d7dde3)"></div>

<div class="sec-head" style="top:1323px"><span class="kicker">Investment Criteria</span><h2>WHAT WE LOOK FOR</h2></div>
<div class="criteria">
  <div class="criterion"><div class="bar"></div><h3>Market changes that enable a big new category</h3><p>Lorem ipsum dolor , consectetur adipiscing elit, sed do eiusmod tempor incididunt ut labore et dolore magna aliqua.</p></div>
  <div class="criterion"><div class="bar"></div><h3>Demonstrate you hire better than yourself</h3><p>Lorem ipsum dolor , consectetur adipiscing elit, sed do eiusmod tempor incididunt ut labore et dolore magna aliqua.</p></div>
  <div class="criterion"><div class="bar"></div><h3>Some evidence of market fit</h3><p>Lorem ipsum dolor , consectetur adipiscing elit, sed do eiusmod tempor incididunt ut labore et dolore magna aliqua.</p></div>
</div>

<div class="sec-head" style="top:1660px"><span class="kicker">Services</span><h2>WHAT WE OFFER</h2></div>
<div class="services">
  <div class="tile" role="img" aria-label="Business people shaking hands" style="background:linear-gradient(180deg,#9aa0a6,#3c3f44)"><div class="txt"><h3>PRIVATE EQUITY</h3><p>Lorem ipsumsiconsectetur adipiscing elit, sed do</p></div><svg width="22" height="22" viewBox="0 0 22 22" fill="none" stroke="#fff"><circle cx="11" cy="11" r="10"/><path d="M6 11h10M12 7l4 4-4 4"/></svg></div>
  <div class="tile" role="img" aria-label="Hand holding a credit card and phone" style="background:linear-gradient(180deg,#c99a72,#3d3f45)"><div class="txt"><h3>CREDIT</h3><p>Lorem ipsumsiconsectetur adipiscing elit, sed do</p></div><svg width="22" height="22" viewBox="0 0 22 22" fill="none" stroke="#fff"><circle cx="11" cy="11" r="10"/><path d="M6 11h10M12 7l4 4-4 4"/></svg></div>
  <div class="tile" role="img" aria-label="Team meeting in front of a screen with charts" style="background:linear-gradient(180deg,#a9b4bf,#3b4048)"><div class="txt"><h3>PUBLIC EQUITY</h3><p>Lorem ipsumsiconsectetur adipiscing elit, sed do</p></div><svg width="22" height="22" viewBox="0 0 22 22" fill="none" stroke="#fff"><circle cx="11" cy="11" r="10"/><path d="M6 11h10M12 7l4 4-4 4"/></svg></div>
  <div class="tile" role="img" aria-label="Tablet showing bar charts beside a keyboard" style="background:linear-gradient(180deg,#8fa6bf,#3a4048)"><div class="txt"><h3>DOUBLE IMPACT</h3><p>Lorem ipsumsiconsectetur adipiscing elit, sed do</p></div><svg width="22" height="22" viewBox="0 0 22 22" fill="none" stroke="#fff"><circle cx="11" cy="11" r="10"/><path d="M6 11h10M12 7l4 4-4 4"/></svg></div>
  <div class="tile" role="img" aria-label="Businessman beside large venture capital lettering" style="background:linear-gradient(180deg,#b9b9b9,#444)"><div class="txt"><h3>VENTURE</h3><p>Lorem ipsumsiconsectetur adipiscing elit, sed do</p></div><svg width="22" height="22" viewBox="0 0 22 22" fill="none" stroke="#fff"><circle cx="11" cy="11" r="10"/><path d="M6 11h10M12 7l4 4-4 4"/></svg></div>
  <div class="tile" role="img" aria-label="Agent handing a small house model to a client" style="background:linear-gradient(180deg,#8a8a8e,#35373b)"><div class="txt"><h3>REAL ESTATE</h3><p>Lorem ipsumsiconsectetur adipiscing elit, sed do</p></div><svg width="22" height="22" viewBox="0 0 22 22" fill="none" stroke="#fff"><circle cx="11" cy="11" r="10"/><path d="M6 11h10M12 7l4 4-4 4"/></svg></div>
  <div class="tile" role="img" aria-label="Hands joining jigsaw puzzle pieces" style="background:linear-gradient(180deg,#b89d78,#3e3d3a)"><div class="txt"><h3>PARTNERSHIP STRATEGIES</h3><p>Lorem ipsumsiconsectetur adipiscing elit, sed do</p></div><svg width="22" height="22" viewBox="0 0 22 22" fill="none" stroke="#fff"><circle cx="11" cy="11" r="10"/><path d="M6 11h10M12 7l4 4-4 4"/></svg></div>
  <div class="tile" role="img" aria-label="Hand interacting with a digital network display" style="background:linear-gradient(180deg,#6a86a3,#2f3540)"><div class="txt"><h3>TECH OPPORTUNITIES</h3><p>Lorem ipsumsiconsectetur adipiscing elit, sed do</p></div><svg width="22" height="22" viewBox="0 0 22 22" fill="none" stroke="#fff"><circle cx="11" cy="11" r="10"/><path d="M6 11h10M12 7l4 4-4 4"/></svg></div>
</div>

<h2 class="projects-title">OUR PROJECTS</h2>
<div class="rule" style="left:110px;top:2375px;width:85px"></div>
<div class="btn" style="left:110px;top:2420px;width:166px;height:45px">Read more
  <svg width="14" height="10" viewBox="0 0 14 10"><path d="M0 5h11M8 1l4 4-4 4" stroke="#fff" stroke-width="2" fill="none"/></svg></div>
<div class="projects-copy">
  <p>Lorem ipsum dolor sit amet, consectetur adipiscing elit, sed do eiusmod tempor incididunt ut labore et dolore magna aliqua. Quis ipsum suspendisse ultrices gravida.</p>
  <p>Lorem ipsum dolor sit amet, consectetur adipiscing elit, sed do eiusmod tempor incididunt ut labore et dolore magna aliqua. Quis ipsum suspendisse ultrices gravida. Risus commodo viverra maecenas accumsan lacus vel facilisis.</p>
</div>
<div class="photo" role="img" aria-label="Colleagues talking in a modern office" style="left:215px;top:2488px;width:268px;height:165px;background:linear-gradient(135deg,#d8cfc2,#7d6f62)"></div>
<div class="photo" role="img" aria-label="Glass skyscrapers seen from below against a blue sky" style="left:496px;top:2523px;width:594px;height:347px;background:linear-gradient(160deg,#e9eef4 0%,#7fa3cc 45%,#1f4f86 100%)"></div>
<div class="photo" role="img" aria-label="Hands reviewing printed charts with a pen" style="left:110px;top:2673px;width:493px;height:305px;background:linear-gradient(135deg,#8c97a6,#e2e6ec 60%,#9fb3cf)"></div>

<section class="team">
  <div class="photo" role="img" aria-label="Portrait of a partner in a grey suit with arms crossed" style="left:300px;top:77px;width:260px;height:456px;background:linear-gradient(180deg,rgba(120,120,120,0),#8a8a8a 40%,#6b6b6b)"></div>
  <h2 class="team-title">OUR TEAM</h2>
  <div class="rule" style="left:110px;top:260px;width:85px"></div>
  <div class="btn btn-outline" style="left:914px;top:52px;width:166px;height:47px;border-width:1px;font-weight:500">View more
    <svg width="14" height="10" viewBox="0 0 14 10"><path d="M0 5h11M8 1l4 4-4 4" stroke="#fff" stroke-width="2" fill="none"/></svg></div>
  <div class="member">
    <h3>DANIEL MORROW</h3>
    <p>Lorem ipsum dolor sit amet, consectetur adipiscing elit, stempor incididunt ut labore et dolore magna aliqua. Quis ipsum suspendisse ultrices gravida. Risus commodo viverra maecenas accumsan lacus vel facilisiipsum dolor sit amet, consectetur adipiscing elit,</p>
    <p>Lorem ipsum dolor sit amet, consectetur adipiscing elit, stempor incididunt ut labore et dolore magna aliqua. Quis ipsum suspendisse ultrices gravida. Risus commodo viverra maecenas</p>
  </div>
  <div class="btn" style="left:572px;top:404px;width:165px;height:45px">Read more
    <svg width="14" height="10" viewBox="0 0 14 10"><path d="M0 5h11M8 1l4 4-4 4" stroke="#fff" stroke-width="2" fill="none"/></svg></div>
</section>

<div class="sec-head" style="top:3676px"><span class="kicker">Latest Updates</span><h2>NEWS &amp; BLOGS</h2></div>
<article class="card" style="left:110px"><div class="pic" role="img" aria-label="Office towers with a rising stock chart" style="background:linear-gradient(160deg,#c9d6e4,#4f7096)"></div><div class="bar"></div><h3>Lorem ipsum dolor sit amet, consectetur adipiscing</h3><p>Lorem ipsum dolor sit amet, consectetur adipiscing elit, sed do eiusmod tempor incididunt ut labore et dolore</p><div class="more">See Details <svg width="14" height="8" viewBox="0 0 14 8"><path d="M0 4h11M8 1l3 3-3 3" stroke="#333" stroke-width="1.6" fill="none"/></svg></div></article>
<article class="card" style="left:442px"><div class="pic" role="img" aria-label="Hands working with a pen on paperwork and a laptop" style="background:linear-gradient(160deg,#eef1f4,#9aa7b6)"></div><div class="bar"></div><h3>Lorem ipsum dolor sit amet, consectetur adipiscing</h3><p>Lorem ipsum dolor sit amet, consectetur adipiscing elit, sed do eiusmod tempor incididunt ut labore et dolore</p><div class="more">See Details <svg width="14" height="8" viewBox="0 0 14 8"><path d="M0 4h11M8 1l3 3-3 3" stroke="#333" stroke-width="1.6" fill="none"/></svg></div></article>
<article class="card" style="left:775px"><div class="pic" role="img" aria-label="Laptop on a bright desk with a person working" style="background:linear-gradient(160deg,#f1ede6,#b7a894)"></div><div class="bar"></div><h3>Lorem ipsum dolor sit amet, consectetur adipiscing</h3><p>Lorem ipsum dolor sit amet, consectetur adipiscing elit, sed do eiusmod tempor incididunt ut labore et dolore</p><div class="more">See Details <svg width="14" height="8" viewBox="0 0 14 8"><path d="M0 4h11M8 1l3 3-3 3" stroke="#333" stroke-width="1.6" fill="none"/></svg></div></article>

<footer class="footer">
  <div class="abs" style="left:110px;top:80px;width:285px">
    <div style="display:flex;align-items:center;gap:10px;font-weight:700;font-size:18px;margin-bottom:18px"><span class="brand-dot" style="width:32px;height:32px;background:#9a9a9a"></span>Harlow Ridge Financial</div>
    <p>Lorem ipsum dolor sit amet, adipiscing elit, sed do eiusmod tempor incididunt ut labore et dolore magna aliqua. Quissuspendisse ultrices gravida.</p>
    <div class="socials"><i></i><i></i><i></i><i></i></div>
  </div>
  <div class="abs" style="left:424px;top:86px">
    <h4>QUICK LINKS</h4>
    <ul><li>Home</li><li>About</li><li>Learn</li><li>Contcat US</li><li>Partners</li></ul>
  </div>
  <div class="abs contact" style="left:562px;top:86px;width:240px">
    <h4>CONTACT US</h4>
    <ul>
      <li><svg width="20" height="20" viewBox="0 0 20 20"><circle cx="10" cy="10" r="9.5" fill="none" stroke="#fff"/><path d="M10 5a3 3 0 0 0-3 3c0 2.5 3 6 3 6s3-3.5 3-6a3 3 0 0 0-3-3z" fill="#fff"/></svg><span style="line-height:24px">1234 Lorem Ipsum sed<br>xxxx United States 0000</span></li>
      <li><svg width="20" height="20" viewBox="0 0 20 20"><circle cx="10" cy="10" r="9.5" fill="none" stroke="#fff"/><path d="M7 6l2 0 1 2-1 1a5 5 0 0 0 2 2l1-1 2 1v2c-4 0-7-3-7-7z" fill="#fff"/></svg>888 888 8888</li>
      <li><svg width="20" height="20" viewBox="0 0 20 20"><circle cx="10" cy="10" r="9.5" fill="none" stroke="#fff"/><rect x="5.5" y="7" width="9" height="6" fill="none" stroke="#fff"/><path d="M5.5 7l4.5 3.5L14.5 7" fill="none" stroke="#fff"/></svg>info@harlowridgefp.com</li>
    </ul>
  </div>
  <div class="abs" style="left:825px;top:86px;width:265px">
    <h4>SUBSCRIBE TO OUR BLOG</h4>
    <p>Sign up today to get resources on how to attract and retain more customers!</p>
    <div class="subscribe"><span>Email Address</span><b><svg width="16" height="16" viewBox="0 0 16 16"><path d="M1 8l14-7-5 14-2-6z" fill="#fff"/></svg></b></div>
  </div>
  <div class="legal"><span>Copyright © 2020. All Rights Reserved</span><span>Terms and Conditions &nbsp;|&nbsp; Privacy Policy</span></div>
</footer>

</body>
</html>
```